Brightfold Power - Company Brochure / Display Folder / DL Flyer

We are a trader in environmental commodities based in Australia and require the following 4 designs for an upcoming exhibition;
1) Brochure Folder
Essentially this will be a presentation folder for a number of A4 sheets and will allow us to present business cards. We would like it based on the same design as our stand background - please see attached (001) for reference.
I have attached a file (002) that is basically what i am after, if you could recreate this or something similar it be sufficient. Please change the blue lines to green and incorporate an image that represents solar / environment / renewable energy etc.
Please include our logo (003) as well as the words 'experts in environmental commodity trading'
The back of the folder should have our address, contact number, homepage etc - please refer to the website for these details www.brightfoldpower.com.au.
The template is included also, please ensure the deisgn fits within these boundaries for printing (004 / Forme 8)
2) A4 Flyer
We are after a re design of an old flyer that highlights what we do as a business. I have included the wording for this (005) but am open to interpretations as to designs. Please keep it relevant to the graphics requested for the presentation folder.
This will be a single page A4 sheet - very easy.
3) DL Brochure
We will be running a promotion at the exhibition for cash rewards and need a double sided DL flyer designed so the can be handed out. The back of the flyer should have our logo as well as the green graphics consistent with the stand design / background while the front needs to highlight the following promotional offer;
Brightfold Power Cash Rewards Offer
Get more out of your STC's -trade with us to receive instant cash back!
Trade 1000 STC - receive $250 cash rewards card
Trade 5000 STC - receive $500 cash rewards card
(x1 card on the first 1000 + x2 more cards on the first 5000)
Cash rewards cards are valid everywhere that accepts Tapcard - cash can even be withdrawn at ATMS!
Offer valid until October 31st 2014
Unregistered Trade Only.
Please keep this text to the left and incorporate an image or graphic on the right side. One that is professional, ties in with the notion of environmental trading but highlights the offer.
Again we open to interpretations with this one.
4) Card Design
Very basic - a design is needed for the rewards card mentioned in the promotion above. I have attached the template / outline required for this (006/ 007) and basically need out logo and a bit of colour on the cash card.
We are open to some ideas but the main thing is being consistent with the stand design that we will be exhibiting in. We like the graphics used and the plain white with the green curved concept. Please ensure the greens from our logo also.
I will do my best to answer any queries you may have, the files should have all the info needed to get started and we usually have a few design amendments after the first drafts are sent through.
Apologies about the timeframe with this one - we are looking to move fast so the earlier submissions will be considered as I can work back and forth with them.
Good Luck
Brightfold Power.

```html
<!DOCTYPE html>
<html lang="en">
<head>
<meta charset="utf-8">
<title>Brightfold Power – Cash Rewards DL Flyer</title>
<link href="https://fonts.googleapis.com/css2?family=Arimo:wght@400;700&display=swap" rel="stylesheet">
<style>
  :root {
    --page: #ffffff;
    --panel-grey: #e4e5e4;
    --panel-light: #f7f7f6;
    --frame: #6d6d6d;
    --green-dark: #0d4d2c;
    --green-mid: #1f8a3a;
    --green-text: #2c8a2c;
    --green-lime: #a9cf2b;
    --yellow: #e5ea5a;
    --ink: #444444;
  }
  * { box-sizing: border-box; margin: 0; padding: 0; }
  html, body {
    width: 1049px; height: 1200px; overflow: hidden;
    background: var(--page);
    font-family: "Arimo", Arial, sans-serif;
    color: var(--ink);
  }
  .canvas { position: relative; width: 1049px; height: 1200px; }

  /* Back side */
  .flyer-back {
    position: absolute; left: 92px; top: 84px; width: 842px; height: 494px;
    border: 1px solid var(--frame);
    background: radial-gradient(ellipse at 55% 55%, #ffffff 0%, #f3f3f3 55%, #dedede 100%);
    overflow: hidden;
  }
  .wave-area {
    position: absolute; left: 0; top: 0; width: 840px; height: 340px;
    background:
      linear-gradient(180deg, rgba(255,255,255,0) 0%, rgba(255,255,255,0) 55%, rgba(255,255,255,0.9) 100%),
      linear-gradient(90deg, var(--green-mid) 0%, var(--green-lime) 35%, var(--yellow) 60%, var(--green-mid) 100%);
    opacity: 0.75;
  }
  .brand {
    position: absolute; left: 563px; top: 372px;
    display: flex; align-items: center; gap: 12px;
  }
  .brand-mark { width: 22px; height: 22px; background: var(--green-mid); }
  .brand-name {
    font-size: 26px; font-weight: 700; color: var(--green-mid);
    line-height: 28px; text-transform: uppercase;
  }
  .tagline {
    position: absolute; left: 565px; top: 447px;
    font-size: 10px; letter-spacing: 1px; color: #333;
  }

  /* Front side */
  .flyer-front-bg {
    position: absolute; left: 68px; top: 598px; width: 890px; height: 540px;
    background: linear-gradient(160deg, var(--panel-grey) 0%, var(--panel-light) 45%, var(--panel-grey) 100%);
  }
  .flyer-front {
    position: absolute; left: 92px; top: 618px; width: 842px; height: 494px;
    border: 1px solid var(--frame);
  }
  .offer-title {
    position: absolute; left: 0; top: 30px; width: 100%;
    text-align: center; font-size: 41px; color: var(--green-dark); font-weight: 400;
  }
  .offer-copy {
    position: absolute; left: 46px; top: 114px; width: 320px;
    font-size: 17px; line-height: 21.7px;
  }
  .offer-copy p { margin-bottom: 21px; }
  .offer-copy p.intro { margin-bottom: 32px; }
  .offer-copy .lead-cap { font-size: 27px; line-height: 20px; }
  .offer-copy .reward { color: var(--green-text); }
  .reward-card {
    position: absolute; left: 470px; top: 100px; width: 252px; height: 148px;
    border-radius: 12px; transform: rotate(4deg);
    background: linear-gradient(170deg, #e9f3c9 0%, #9fcf4a 30%, #1f8a3a 45%, #ffffff 60%, #f1f1f1 100%);
    box-shadow: 4px 6px 10px rgba(0,0,0,0.35);
  }
  .card-value { position: absolute; left: 32px; bottom: 26px; font-size: 11px; color: #555; }
  .card-network { position: absolute; right: 24px; bottom: 34px; font-size: 22px; font-weight: 700; color: #8c1d3f; }
  .card-note {
    position: absolute; left: 446px; top: 307px;
    font-size: 17px; line-height: 21.5px;
  }
  .lead-source { margin-top: 22px; display: flex; align-items: baseline; gap: 4px; }
  .lead-line { width: 244px; border-bottom: 1px dotted #555; }
  .terms {
    position: absolute; left: 46px; top: 455px;
    font-size: 10.5px; letter-spacing: 2px; color: var(--green-dark);
  }
</style>
</head>
<body>
<div class="canvas">

  <section class="flyer-back">
    <div class="wave-area" role="img" aria-label="Decorative flowing green and yellow ribbon wave artwork"></div>
    <div class="brand">
      <span class="brand-mark"></span>
      <span class="brand-name">Brightfold<br>Power</span>
    </div>
    <p class="tagline">experts in environmental commodity trading</p>
  </section>

  <div class="flyer-front-bg"></div>
  <section class="flyer-front">
    <h1 class="offer-title">Brightfold Power Cash Rewards Offer!</h1>

    <div class="offer-copy">
      <p class="intro"><span class="lead-cap">G</span>et more out of your STC's<br>trade with us to receive<br>instant cash back!</p>
      <p>Trade 1000 STC<br><span class="reward">receive $250 cash rewards card</span></p>
      <p>Trade 5000 STC<br><span class="reward">receive $500 cash rewards card</span></p>
      <p>(x1 card on the first 1000<br>+<br>x2 more cards on the first 5000)</p>
    </div>

    <div class="reward-card" role="img" aria-label="Cash rewards card with green wave artwork">
      <span class="card-value">$250 value</span>
      <span class="card-network">Tapcard</span>
    </div>

    <div class="card-note">
      <p>Cash rewards cards are valid everywhere...<br>that accepts Tapcard<br>Cash can even be withdrawn at ATMS!</p>
      <p class="lead-source">Lead Source <span class="lead-line"></span></p>
    </div>

    <p class="terms">* Offer valid until October 31st 2014 I Unregistered Trade Only | contact 1300 555 014 for further details.</p>
  </section>

</div>
</body>
</html>
```